New Zealand Marlborough Sauvignon Blanc wine packaging design

We need packaging design for our new wine brand, Dunmore Vale. The wine is a New Zealand Marlborough Sauvignon Blanc. We would like the packaging will portray elegance and style with an understated label. We are looking for a label that portrays the elegance of the French Riviera. The label should be round or pill shaped.
Updates

Industry/Entity Type

Wine

Font styles to use
Serif
Sans Serif

Requirements
Must have
• The words in order of importance: Dunmore Vale, Sauvignon Blanc, Marlborough, New Zealand. It should be fit to the bottle posted in the links
Nice to have
• a pill shape or circular shape
Should not have
• Illustrations of wine bottles, wine glasses, or grapes

```html
<!DOCTYPE html>
<html lang="en">
<head>
<meta charset="utf-8">
<title>Dunmore Vale — Sauvignon Blanc Label</title>
<link rel="stylesheet" href="https://fonts.googleapis.com/css2?family=Playfair+Display:wght@400;500&display=swap">
<style>
  :root {
    --label-gold: #b9a21c;
    --label-black: #000000;
    --page-bg: #ffffff;
  }
  html, body {
    margin: 0;
    padding: 0;
    width: 1200px;
    height: 675px;
    overflow: hidden;
    background: var(--page-bg);
  }
  .label-canvas {
    display: block;
    width: 1200px;
    height: 675px;
  }
  .label-rim { fill: var(--label-gold); }
  .label-ring { fill: none; stroke: var(--label-black); stroke-width: 2; }
  .label-core { fill: var(--label-black); }
  .variety-band { fill: var(--label-black); stroke: var(--label-gold); stroke-width: 2.5; }
  .brand-name {
    font-family: "Playfair Display", serif;
    font-weight: 400;
    font-size: 62px;
    fill: var(--label-gold);
    letter-spacing: 1px;
  }
  .variety-name {
    font-family: "Playfair Display", serif;
    font-weight: 400;
    font-size: 34px;
    fill: var(--label-black);
    stroke: var(--label-gold);
    stroke-width: 1.1;
  }
  .region-line {
    font-family: "Playfair Display", serif;
    font-weight: 400;
    font-size: 22px;
    fill: var(--label-black);
    letter-spacing: 1.5px;
  }
</style>
</head>
<body>
<svg class="label-canvas" viewBox="0 0 1200 675" xmlns="http://www.w3.org/2000/svg" aria-label="Dunmore Vale Sauvignon Blanc round label">
  <defs>
    <path id="region-arc" d="M -220 0 A 220 220 0 0 0 220 0"/>
  </defs>
  <g class="wine-label" transform="translate(600 337)">
    <circle class="label-rim" r="249"/>
    <path class="label-ring" d="M -150 150 A 212 212 0 1 1 150 150"/>
    <circle class="label-core" r="179"/>
    <text class="brand-name" x="0" y="-42" text-anchor="middle">Dunmore</text>
    <text class="brand-name" x="0" y="16" text-anchor="middle">Vale</text>
    <rect class="variety-band" x="-183" y="51" width="365" height="55" rx="27.5"/>
    <text class="variety-name" x="0" y="90" text-anchor="middle">Sauvignon Blanc</text>
    <text class="region-line">
      <textPath href="#region-arc" startOffset="50%" text-anchor="middle">Marlborough &#160;•&#160; New Zealand</textPath>
    </text>
  </g>
</svg>
</body>
</html>
```